Harrowgate Care Assurance Ltd needs a business card and logo

We need a logo for documents, invoices etc and a business card to match. We are a health auditing, training and consulting company based in NZ and working in both Australia and NZ. We ensure health organisations meet all their compliance requirements and develop expertise in the health auditing sector. The design should in some way reflect either symbols for quality management in the health sector.

Target Market(s)

Health providers and those wishing to increase their capability in meeting and understanding compliance requirements

Industry/Entity Type

Business

Contact Information for Business Card

Logo plus contact details

Logo Text

Health auditing, consultancy and training

Requirements
Must have
• Name and contact details director: Marla Fenwick, mfenwick@hca-example.co.nz, PO Box 318, Warkworth, NZ, cell +6427391652

```html
<!DOCTYPE html>
<html lang="en">
<head>
<meta charset="utf-8">
<title>Harrowgate Care Assurance Ltd — Business Card</title>
<link rel="stylesheet" href="https://fonts.googleapis.com/css2?family=Source+Sans+3:wght@400;600&display=swap">
<style>
  :root {
    --backdrop: #2a2a2a;
    --brand-blue: #065fa3;
    --brand-blue-light: #1a86cc;
    --band-blue: #1b82cb;
    --band-dark: #3a3a3a;
    --card-white: #ffffff;
    --ink: #2b2b2b;
    --name-blue: #0d5d9e;
  }
  * { margin: 0; padding: 0; box-sizing: border-box; }
  html, body {
    width: 1200px; height: 1001px; overflow: hidden;
    background: var(--backdrop);
    font-family: "Source Sans 3", "Myriad Pro", Arial, sans-serif;
  }
  .canvas { position: relative; width: 1200px; height: 1001px; }

  .card {
    position: absolute; left: 276px; width: 618px; height: 379px;
    border-radius: 14px; overflow: hidden;
  }
  .card--front {
    top: 99px;
    background: radial-gradient(ellipse 300px 220px at 50% 48%, var(--brand-blue-light) 0%, var(--brand-blue) 100%);
  }
  .card--back { top: 511px; background: var(--card-white); }

  .brand { position: absolute; display: flex; align-items: center; }
  .brand__mark { border-radius: 50%; flex: none; }
  .brand__name {
    font-weight: 400; font-size: 24px; line-height: 1.05; letter-spacing: 1px;
    text-transform: uppercase; margin-left: 10px;
  }
  .card--front .brand { left: 140px; top: 138px; }
  .card--front .brand__mark { width: 110px; height: 110px; background: #f2f4f6; }
  .card--front .brand__name { color: #ffffff; }

  .card--back .brand { left: 35px; top: 43px; }
  .card--back .brand__mark {
    width: 102px; height: 102px;
    background: radial-gradient(circle at 40% 35%, var(--brand-blue-light), var(--brand-blue));
  }
  .card--back .brand__name { color: var(--ink); font-size: 23px; }

  .band { position: absolute; top: 0; height: 19px; }
  .band--blue { left: 0; width: 390px; background: var(--band-blue); }
  .band--dark { left: 393px; right: 0; background: var(--band-dark); }

  .contact { position: absolute; left: 364px; top: 240px; color: var(--ink); font-size: 17px; }
  .contact__name {
    color: var(--name-blue); font-weight: 600; font-size: 18px;
    letter-spacing: 0.8px; text-transform: uppercase; margin-bottom: 6px;
  }
  .contact__line { display: flex; align-items: center; gap: 6px; line-height: 22px; }
  .contact__address { margin-bottom: 4px; }
  .contact__icon { width: 15px; height: 14px; flex: none; }
</style>
</head>
<body>
<main class="canvas">
  <section class="card card--front">
    <div class="brand">
      <div class="brand__mark"></div>
      <div class="brand__name">Harrowgate Care<br>Assurance Ltd</div>
    </div>
  </section>

  <section class="card card--back">
    <div class="band band--blue"></div>
    <div class="band band--dark"></div>
    <div class="brand">
      <div class="brand__mark"></div>
      <div class="brand__name">Harrowgate Care<br>Assurance Ltd</div>
    </div>
    <div class="contact">
      <div class="contact__name">Marla Fenwick</div>
      <div class="contact__line contact__address">PO Box 318, Warkworth, NZ</div>
      <div class="contact__line">
        <svg class="contact__icon" viewBox="0 0 15 14" aria-hidden="true">
          <rect x="4" y="0.5" width="7" height="13" rx="1.2" fill="none" stroke="#1b82cb" stroke-width="1.4"/>
          <rect x="5.5" y="2" width="4" height="8.5" fill="#1b82cb"/>
        </svg>
        <span>+6427391652</span>
      </div>
      <div class="contact__line">
        <svg class="contact__icon" viewBox="0 0 15 14" aria-hidden="true">
          <rect x="0.5" y="2.5" width="14" height="9.5" fill="#1b82cb"/>
          <path d="M0.5 2.5 L7.5 8 L14.5 2.5" fill="none" stroke="#ffffff" stroke-width="1.2"/>
        </svg>
        <span>mfenwick@hca-example.co.nz</span>
      </div>
    </div>
  </section>
</main>
</body>
</html>
```